International business needs business cards

Our company, DRV Ventures Inc. is in the business of supplying a range construction products with particular emphasis on CEMENT. We have developed our own brand - TORVAN SUPPLIES - with which to infiltrate the market. We are launching our brand of cement (TORVAN Type IS Cement) into the Caribbean which is unlike anything this market has ever seen. A monopoly has existed here for the past 60-odd years and the market has now opened to allow the importation of other brands and consumers are anxious and ready for change/improvement. We are very excited to be launching and want to make a great first impression. We will be conducting workshops and seminars (from government level to the hardware store owners) and we want our business card to give us the strong, confident introduction that we need.

Target Market(s)

construction; builders; engineers; home owners

Industry/Entity Type

Construction

Contact Information for Business Card

Marisol Depree
CEO
cell # 1 555 4180736
Ground floor,Lindell Plaza Suite 2734
George Town,Grand Cayman
Cayman Islands,KY1-4823
EMAIL: m.depree@drvventuresinc.example
web site drvventuresinc.example

COMPANY: skype info drv.ventures.example

second card
Yvette Brannock-Depree
CFO
CELL# 1 555 607 3941
George Town,Grand Cayman
Cayman Islands,KY1-4823
EMAIL: y.brannockdepree@drvventuresinc.example
website drvventuresinc.example

Requirements
Must have
• Business cards must display BOTH logos - DRV is the company and TORVAN is the brand.

```html
<!DOCTYPE html>
<html lang="en">
<head>
<meta charset="utf-8">
<title>DRV Ventures Inc. — Business Card</title>
<link href="https://fonts.googleapis.com/css2?family=Open+Sans:wght@400;600;700&display=swap" rel="stylesheet">
<style>
  :root {
    --backdrop: #e9e6e1;
    --card: #ffffff;
    --brand-red: #8e1b1f;
    --ink: #151515;
    --ink-soft: #5a5a5a;
    --on-dark: #f2f2f2;
  }
  * { box-sizing: border-box; margin: 0; padding: 0; }
  html, body {
    width: 1200px; height: 950px; overflow: hidden;
    background: var(--backdrop);
    font-family: "Open Sans", Arial, sans-serif;
  }
  .card {
    position: absolute; left: 250px;
    width: 700px; height: 400px;
    background: var(--card);
    box-shadow: 0 6px 18px rgba(0,0,0,.18);
    overflow: hidden;
  }
  .card--front { top: 45px; }
  .card--back { top: 505px; }

  .brand-mark, .company-mark {
    display: flex; align-items: center; gap: 12px;
    font-weight: 700; white-space: nowrap;
  }

  /* front */
  .front-marks {
    position: absolute; top: 125px; left: 40px; right: 40px;
    display: flex; justify-content: center; align-items: center; gap: 56px;
  }
  .brand-mark { color: var(--ink-soft); font-size: 24px; letter-spacing: 2px; }
  .brand-mark .dot {
    width: 72px; height: 72px; border-radius: 50%;
    background: var(--ink-soft);
    flex: none;
  }
  .company-mark { color: var(--ink); font-size: 26px; }
  .company-mark .square {
    width: 70px; height: 62px; background: var(--brand-red);
    flex: none;
  }
  .front-web {
    position: absolute; top: 268px; left: 0; right: 0;
    text-align: center; font-size: 15px; letter-spacing: 3px;
    color: var(--ink-soft);
  }

  /* back */
  .back-logo {
    position: absolute; top: 52px; left: 0; right: 0;
    justify-content: center;
    font-size: 34px;
  }
  .back-logo .square { width: 92px; height: 82px; }

  .band-red {
    position: absolute; left: 0; right: 0; bottom: 0; height: 150px;
    background: var(--brand-red);
  }
  .band-dark {
    position: absolute; right: 0; bottom: 0; width: 330px; height: 210px;
    background: var(--ink);
    clip-path: polygon(28% 0, 100% 0, 100% 100%, 0 100%, 0 28%);
  }
  .contact {
    position: absolute; left: 36px; bottom: 22px;
    color: var(--on-dark); font-size: 15px; line-height: 1.55;
  }
  .contact .name { font-size: 22px; font-weight: 700; line-height: 1.3; }
  .contact .role { margin-bottom: 2px; }
  .contact .line { display: flex; align-items: center; gap: 8px; }
  .contact svg { width: 14px; height: 14px; fill: var(--on-dark); flex: none; }
  .address {
    position: absolute; right: 28px; bottom: 34px;
    text-align: right; color: var(--on-dark);
    font-size: 15px; line-height: 1.6; font-style: normal;
  }
</style>
</head>
<body>

<section class="card card--front">
  <div class="front-marks">
    <div class="brand-mark"><span class="dot"></span>TORVAN</div>
    <div class="company-mark"><span class="square"></span>DRV Ventures Inc.</div>
  </div>
  <p class="front-web">www.drvventuresinc.example</p>
</section>

<section class="card card--back">
  <div class="company-mark back-logo"><span class="square"></span>DRV Ventures Inc.</div>

  <div class="band-red"></div>
  <div class="band-dark"></div>

  <div class="contact">
    <p class="name">Marisol Depree</p>
    <p class="role">CEO</p>
    <p class="line">
      <svg viewBox="0 0 14 14" aria-hidden="true"><path d="M3 0h8a1 1 0 0 1 1 1v12a1 1 0 0 1-1 1H3a1 1 0 0 1-1-1V1a1 1 0 0 1 1-1zm1 2v8h6V2zm3 9a1 1 0 1 0 0 2 1 1 0 0 0 0-2z"/></svg>
      1 555 4180736
    </p>
    <p class="line">
      <svg viewBox="0 0 14 14" aria-hidden="true"><path d="M0 3h14v9H0zm1 1.2v.3l6 4 6-4v-.3zm0 1.6V11h12V5.8l-6 4z"/></svg>
      m.depree@drvventuresinc.example
    </p>
  </div>

  <address class="address">
    Ground floor<br>
    Lindell Plaza Suite 2734<br>
    George Town,Grand Cayman<br>
    Cayman Islands,KY1-4823
  </address>
</section>

</body>
</html>
```